Psychiatric Office Needs a Website- 1st Time Ever!

Been in practice since 2003 with no website, but finally ready to dive in. We are Maplecrest Behavioral Healthcare, a mental health outpatient practice based in Fayetteville, Georgia that sees diverse individuals and families from childhood to advanced age for a variety of conditions. We've grown by word of mouth and referral but would now like to have a digital footprint. Be the pioneer of our website and we will be sure to share. We would like to see designs that are modern, animated, fairly colorful, easy to read, and caters to all ages. Also, we would like the design to take the whole page (not be centered) and can be viewed well on phone/tablet. Please see our outline for more information. Our motto/slogan is: Maplecrest Behavioral Healthcare- A step forward in your wellness journey, so the design should try to reflect that.
Updates

Project Deadline Extended
Reason: site in progress

Target Market(s)

Children through elderly

Industry/Entity Type

Medical

Logo Text

Stepping forward in your wellness journey

Number of Pages Required

1 page

Colors

Designer to choose colors to be used in the design.

Requirements
Must have
• Animation or moving pictures.
• Color.
• Concise.
• User friendly
• Diversity in the stock photos

```html
<!DOCTYPE html>
<html lang="en">
<head>
<meta charset="utf-8">
<title>Maplecrest Behavioral Healthcare</title>
<link rel="stylesheet" href="https://fonts.googleapis.com/css2?family=Asap:ital,wght@0,400;0,500;0,600;1,400&family=Open+Sans:wght@400;600;700&display=swap">
<style>
:root{
  --orange:#f07a1f;
  --orange-deep:#e86a12;
  --yellow:#f8c400;
  --ink:#333333;
  --muted:#6b6b6b;
  --dark:#2b2b2b;
  --line:#d9d9d9;
  --white:#ffffff;
}
*{box-sizing:border-box;margin:0;padding:0}
html,body{width:1200px;height:3455px;overflow:hidden}
body{position:relative;background:var(--white);font-family:"Open Sans",Arial,sans-serif;color:var(--ink)}
.abs{position:absolute}
.heading{font-family:"Asap",Arial,sans-serif;font-weight:400}
.body-text{font-size:14px;line-height:23px}
.read-more{color:var(--white);font-weight:700;text-decoration:underline;white-space:nowrap}

/* header */
.site-header{left:0;top:0;width:1200px;height:120px;background:var(--white);border-bottom:1px solid #eee}
.top-bar{right:70px;top:8px;display:flex;gap:26px;font-size:13px;color:var(--ink);align-items:center;white-space:nowrap}
.top-bar span{display:flex;align-items:center;gap:8px}
.brand{left:80px;top:20px;display:flex;align-items:center;gap:12px}
.brand-dot{width:24px;height:24px;border-radius:50%;background:var(--orange);flex:none}
.brand-name{font-family:"Asap",Arial,sans-serif;font-size:18px;color:var(--orange);font-weight:500;width:170px;line-height:22px}
.nav{top:46px;left:0;width:1200px;height:74px;font-family:"Asap",Arial,sans-serif;font-size:16px}
.nav a{position:absolute;top:0;height:74px;line-height:74px;color:var(--ink);text-decoration:none;white-space:nowrap}
.nav .active{background:var(--orange);color:var(--white);top:-9px;height:83px;line-height:92px;width:104px;text-align:center}

/* hero */
.hero{left:0;top:120px;width:1200px;height:571px;background:linear-gradient(135deg,#6c8fbf 0%,#c9a57f 35%,#e7c39a 55%,#9bb7d6 80%,#d23a3a 100%)}
.hero-panel{left:207px;top:161px;width:783px;height:203px;background:rgba(40,40,40,.45);text-align:center;color:var(--white)}
.hero-title{font-size:50px;margin-top:14px;line-height:60px}
.hero-tagline{font-family:"Asap",Arial,sans-serif;font-style:italic;font-size:20px;margin-top:2px}
.btn{display:inline-block;background:var(--orange);color:var(--white);font-family:"Asap",Arial,sans-serif;text-transform:uppercase}
.hero .btn{position:absolute;left:300px;top:124px;width:184px;height:56px;line-height:56px;font-size:20px}

/* vision / mission */
.vision{left:0;top:691px;width:600px;height:369px;background:var(--orange);color:var(--white)}
.mission{left:600px;top:691px;width:600px;height:369px;background:var(--white)}
.vm-title{font-size:34px;display:flex;align-items:center;gap:14px}
.vm-title::after{content:"";position:absolute;left:0;top:50px;width:160px;height:2px;background:currentColor}
.emblem{left:464px;top:726px;width:272px;height:272px;border-radius:50%;background:var(--orange);border:6px solid var(--white);box-shadow:0 0 0 3px var(--orange);display:flex;align-items:center;justify-content:center;text-align:center}
.emblem span{font-family:"Asap",Arial,sans-serif;color:var(--white);font-size:22px;line-height:28px;width:170px}

/* services */
.services{left:0;top:1060px;width:1200px;height:829px;background:radial-gradient(ellipse at 50% 40%,#5b5b5b 0%,#3a3a3a 60%,#262626 100%)}
.section-title{font-size:36px;text-align:center;width:100%}
.services .section-title{color:var(--white);top:45px}
.services .section-title::after{content:"";display:block;width:150px;height:2px;background:var(--white);margin:6px auto 0}
.svc{width:330px;color:var(--white)}
.svc h3{font-family:"Asap",Arial,sans-serif;font-weight:400;color:var(--orange);font-size:17px;margin-bottom:4px;white-space:nowrap}
.svc p{font-size:13.5px;line-height:20px;width:240px}

/* conditions */
.conditions{left:0;top:1889px;width:1200px;height:552px;background:linear-gradient(90deg,var(--orange-deep) 0%,#f4931a 55%,var(--yellow) 100%)}
.conditions .section-title{color:var(--white);top:65px}
.conditions .section-title::after{content:"";display:block;width:370px;height:2px;background:var(--white);margin:4px auto 0}
.condition{top:154px;width:253px;color:var(--white);text-align:center}
.condition .photo{height:168px;border:2px solid var(--white);box-shadow:0 4px 8px rgba(0,0,0,.25)}
.condition h3{font-family:"Asap",Arial,sans-serif;font-weight:400;font-size:20px;margin:20px 0 10px;line-height:22px;min-height:22px}
.condition p{font-size:13px;line-height:20px}
.slider-arrow{top:220px;width:30px;height:30px;background:var(--white);display:flex;align-items:center;justify-content:center}
.dots{top:522px;left:574px;display:flex;gap:6px}
.dots i{width:13px;height:13px;border:1px solid var(--white);display:block}
.dots i.on{background:var(--white)}

/* faq / news */
.faq{left:80px;top:2490px;width:520px}
.block-title{font-size:36px;color:var(--orange)}
.faq-item{border:1px solid var(--line);height:44px;display:flex;align-items:center;gap:14px;padding-left:18px;font-family:"Asap",Arial,sans-serif;font-size:19px;color:var(--orange);margin-top:-1px}
.faq-answer{border:1px solid var(--line);border-top:none;padding:10px 18px;font-size:12px;line-height:19px;color:var(--muted);height:86px}
.divider{left:610px;top:2441px;width:10px;height:433px;background:#ececec}
.news{left:668px;top:2490px;width:470px}
.news-item{display:flex;gap:16px;margin-top:24px;padding-bottom:24px;border-bottom:1px solid var(--line)}
.news-item:last-child{border:none}
.news-item .photo{width:115px;height:113px;flex:none}
.news-item h4{font-family:"Asap",Arial,sans-serif;font-weight:400;color:var(--orange);font-size:19px}
.news-item .date{font-size:11px;color:var(--muted);margin:6px 0 3px}
.news-item p{font-size:13.5px;line-height:20px}
.news-item .more{color:var(--orange);font-size:13px;margin-top:12px;display:block}

/* cta */
.cta{left:0;top:2874px;width:1200px;height:108px;background:var(--orange)}
.cta p{position:absolute;left:80px;top:32px;width:780px;color:var(--white);font-size:14px;line-height:23px}
.cta .form-btn{position:absolute;left:894px;top:28px;width:230px;height:55px;background:var(--white);color:var(--ink);font-family:"Asap",Arial,sans-serif;font-size:19px;display:flex;align-items:center;justify-content:center}

/* footer */
.footer{left:0;top:2982px;width:1200px;height:403px;background:linear-gradient(180deg,#3d3530 0%,#4a3c33 50%,#2f2925 100%)}
.footer h5{font-family:"Asap",Arial,sans-serif;font-weight:400;font-size:20px;color:var(--white);text-transform:uppercase}
.field{position:absolute;left:80px;width:445px;height:40px;background:var(--white);font-size:13px;color:var(--muted);padding:10px 14px}
.submit{position:absolute;left:80px;top:346px;width:184px;height:48px;line-height:48px;text-align:center;font-size:18px}
.links{list-style:none;color:var(--white);font-size:14px}
.links li{height:29px;display:flex;align-items:center;gap:12px}
.links li::before{content:"";width:8px;height:8px;border-radius:50%;background:var(--orange)}
.find{color:var(--white);font-size:14px;line-height:22px}
.find .row{position:absolute;left:0;display:flex;gap:16px;align-items:flex-start;width:300px}
.social{position:absolute;width:50px;height:50px;border-radius:50%;background:var(--orange)}
.copyright{left:0;top:3385px;width:1200px;height:70px;background:#2a2522;border-top:1px solid #5a5a5a;color:var(--white);text-align:center;line-height:70px;font-size:13px;font-weight:600}
</style>
</head>
<body>

<header class="site-header abs">
  <div class="brand abs"><div class="brand-dot"></div><div class="brand-name">Maplecrest Behavioral Healthcare</div></div>
  <div class="top-bar abs">
    <span><svg width="16" height="16" viewBox="0 0 16 16"><circle cx="8" cy="8" r="7" fill="none" stroke="#f07a1f" stroke-width="2"/><path d="M8 4v4l3 2" stroke="#f07a1f" stroke-width="2" fill="none"/></svg>Monday - Friday : 10.00 A.M to 8.00 P.M</span>
    <span><svg width="16" height="16" viewBox="0 0 16 16"><path d="M3 1l3 1 1 4-2 1c1 2 2 3 4 4l1-2 4 1 1 3-2 2C7 15 1 9 1 3z" fill="#f07a1f"/></svg>+1-770-555-0148</span>
    <span>LOGIN <svg width="14" height="16" viewBox="0 0 14 16"><circle cx="7" cy="4" r="4" fill="#f07a1f"/><path d="M0 16c0-5 3-7 7-7s7 2 7 7z" fill="#f07a1f"/></svg> Patient</span>
  </div>
  <nav class="nav abs">
    <a class="active" href="#" style="left:357px">Home</a>
    <a href="#" style="left:504px">About Us</a>
    <a href="#" style="left:606px">Services</a>
    <a href="#" style="left:700px">Conditions We Treat</a>
    <a href="#" style="left:888px">New Patients</a>
    <a href="#" style="left:1020px">Contact Us</a>
  </nav>
</header>

<section class="hero abs" role="img" aria-label="Photo of smiling people of all ages gathered in a circle looking down at the camera">
  <div class="hero-panel abs">
    <h1 class="hero-title heading">Maplecrest Behavioral Healthcare</h1>
    <p class="hero-tagline">A step forward in your wellness journey</p>
    <span class="btn">Contact Us</span>
  </div>
</section>

<section class="vision abs">
  <h2 class="vm-title heading abs" style="left:80px;top:58px;position:absolute">
    <svg width="30" height="30" viewBox="0 0 30 30"><rect x="6" y="5" width="18" height="8" rx="2" transform="rotate(-35 15 9)" fill="#fff"/><path d="M14 16l-6 12M16 16l6 12M15 16v12" stroke="#fff" stroke-width="2.5"/></svg>VISION</h2>
  <p class="body-text abs" style="left:80px;top:122px;width:360px;font-size:13.5px;line-height:24px">Lorem Ipsum is simply dummy text of the printing and typesetting industry. Lorem Ipsum has been the industry's standard dummy text ever since the 1500s, when an unknown printer took a galley of type and scrambled it to make a type specimen book. It has survived not only five centuries, but also the leap into electronic typesetting, remaining essentially unchanged.</p>
</section>
<section class="mission abs">
  <h2 class="vm-title heading abs" style="left:170px;top:58px;position:absolute;color:var(--orange)">
    <svg width="32" height="32" viewBox="0 0 32 32"><circle cx="15" cy="17" r="12" fill="none" stroke="#f07a1f" stroke-width="3"/><circle cx="15" cy="17" r="5" fill="none" stroke="#f07a1f" stroke-width="3"/><path d="M15 17L29 3" stroke="#f07a1f" stroke-width="3"/></svg>MISSION</h2>
  <p class="body-text abs" style="left:171px;top:122px;width:360px;font-size:13.5px;line-height:24px;color:var(--muted)">Lorem Ipsum is simply dummy text of the printing and typesetting industry. Lorem Ipsum has been the industry's standard dummy text ever since the 1500s, when an unknown printer took a galley of type and scrambled it to make a type specimen book. It has survived not only five centuries, but also the leap into electronic typesetting, remaining essentially unchanged.</p>
</section>
<div class="emblem abs"><span>Maplecrest Behavioral Healthcare</span></div>

<section class="services abs" role="img" aria-label="Softly blurred photo of a counselling session in a bright office">
  <h2 class="section-title heading abs">SERVICES</h2>
  <svg class="abs" style="left:0;top:0" width="1200" height="829" viewBox="0 0 1200 829">
    <g stroke="#ffffff" stroke-width="2" opacity=".8">
      <line x1="599" y1="384" x2="502" y2="202"/><line x1="599" y1="384" x2="695" y2="197"/>
      <line x1="599" y1="384" x2="396" y2="340"/><line x1="599" y1="384" x2="801" y2="340"/>
      <line x1="599" y1="384" x2="444" y2="529"/><line x1="599" y1="384" x2="767" y2="529"/>
      <line x1="599" y1="384" x2="608" y2="598"/>
    </g>
    <circle cx="599" cy="384" r="104" fill="#ffffff" stroke="#cfcfcf" stroke-width="6"/>
    <g fill="#c9b39b" stroke="#f07a1f" stroke-width="5">
      <circle cx="502" cy="202" r="62"/><circle cx="695" cy="197" r="62"/>
      <circle cx="396" cy="340" r="62"/><circle cx="801" cy="340" r="62"/>
      <circle cx="444" cy="529" r="62"/><circle cx="767" cy="529" r="62"/>
      <circle cx="608" cy="598" r="62"/>
    </g>
    <g fill="#f07a1f">
      <circle cx="548" cy="298" r="6"/><circle cx="650" cy="294" r="6"/><circle cx="497" cy="362" r="6"/>
      <circle cx="702" cy="362" r="6"/><circle cx="520" cy="458" r="6"/><circle cx="683" cy="458" r="6"/><circle cx="603" cy="490" r="6"/>
    </g>
  </svg>
  <div class="svc abs" style="left:138px;top:165px"><h3>Diagnostic evaluation and treatment</h3><p>Lorem Ipsum is simply dummy text of the printing and text typesetting industry.<span class="read-more">READ MORE</span></p></div>
  <div class="svc abs" style="left:80px;top:333px"><h3>Psychopharmacology</h3><p>Lorem Ipsum is simply dummy text of the printing and text typesetting industry.<span class="read-more">READ MORE</span></p></div>
  <div class="svc abs" style="left:101px;top:522px"><h3>Bariatric pre-surgical consultation</h3><p>Lorem Ipsum is simply dummy text of the printing and text typesetting industry.<span class="read-more">READ MORE</span></p></div>
  <div class="svc abs" style="left:771px;top:149px"><h3>Disability and work-related reports</h3><p>Lorem Ipsum is simply dummy text of the printing and text typesetting industry.<span class="read-more">READ MORE</span></p></div>
  <div class="svc abs" style="left:887px;top:306px"><h3>Early childhood Assessments</h3><p>Lorem Ipsum is simply dummy text of the printing and text typesetting industry.<span class="read-more">READ MORE</span></p></div>
  <div class="svc abs" style="left:864px;top:494px"><h3>Substance abuse assessments</h3><p>Lorem Ipsum is simply dummy text of the printing and text typesetting industry.<span class="read-more">READ MORE</span></p></div>
  <div class="svc abs" style="left:502px;top:687px"><h3>Developmental disabilities</h3><p style="width:215px">Lorem Ipsum is simply dummy text of the printing and text typesetting industry.<span class="read-more">READ MORE</span></p></div>
</section>

<section class="conditions abs">
  <h2 class="section-title heading abs">CONDITIOND WE TREAT</h2>
  <div class="slider-arrow abs" style="left:32px"><svg width="10" height="14" viewBox="0 0 10 14"><path d="M8 1L2 7l6 6" stroke="#555" stroke-width="2" fill="none"/></svg></div>
  <div class="slider-arrow abs" style="left:1138px"><svg width="10" height="14" viewBox="0 0 10 14"><path d="M2 1l6 6-6 6" stroke="#f07a1f" stroke-width="2" fill="none"/></svg></div>
  <div class="condition abs" style="left:76px"><div class="photo" role="img" aria-label="Photo of a woman holding her head in distress" style="background:linear-gradient(90deg,#1e1e1e,#6b5a4e)"></div><h3>Mood Disorders</h3><p>Lorem Ipsum is simply dummy text of the printing and typesetting industry. Lorem Ipsum has been the industry's standard dummy text ever since.</p></div>
  <div class="condition abs" style="left:343px"><div class="photo" role="img" aria-label="Photo of a caregiver comforting a woman on a sofa" style="background:linear-gradient(135deg,#8fa9c4,#c4b6a3,#4c6f9c)"></div><h3>Anxiety Disorders</h3><p>Lorem Ipsum is simply dummy text of the printing and typesetting industry. Lorem Ipsum has been the industry's standard dummy text ever since.</p></div>
  <div class="condition abs" style="left:608px"><div class="photo" role="img" aria-label="Photo of a therapist talking with an older man" style="background:linear-gradient(135deg,#b4a48c,#e0d6c6,#6e7f93)"></div><h3>Psychotic Disorders</h3><p>Lorem Ipsum is simply dummy text of the printing and typesetting industry. Lorem Ipsum has been the industry's standard dummy text ever since.</p></div>
  <div class="condition abs" style="left:875px"><div class="photo" role="img" aria-label="Photo of a mother hugging her young daughter" style="background:linear-gradient(135deg,#c9a27e,#8b5e3f,#e0c7a6)"></div><h3 style="margin-top:8px">Common Disorders<br>of Childhood</h3><p>Lorem Ipsum is simply dummy text of the printing and typesetting industry. Lorem Ipsum has been the industry's standard dummy text ever since.</p></div>
  <div class="dots abs"><i></i><i class="on"></i><i></i></div>
</section>

<section class="faq abs">
  <h2 class="block-title heading">FAQ</h2>
  <div style="margin-top:18px">
    <div class="faq-item"><svg width="14" height="14" viewBox="0 0 14 14"><rect y="5" width="14" height="4" fill="#f07a1f"/></svg>What do I need to bring with me to my first visit?</div>
    <div class="faq-answer">Lorem Ipsum is simply dummy text of the printing and typesetting industry. Lorem Ipsum has been the industry's standard dummy text ever since the 1500s.It has survived not only five centuries, but also the leap into electronic typesetting, remaining essentially unchanged.</div>
    <div class="faq-item" style="margin-top:22px"><svg width="14" height="14" viewBox="0 0 14 14"><path d="M5 0h4v5h5v4H9v5H5V9H0V5h5z" fill="#f07a1f"/></svg>How long do I have to wait to be seen?</div>
    <div class="faq-item"><svg width="14" height="14" viewBox="0 0 14 14"><path d="M5 0h4v5h5v4H9v5H5V9H0V5h5z" fill="#f07a1f"/></svg>Why is my child not doing well in school?</div>
    <div class="faq-item"><svg width="14" height="14" viewBox="0 0 14 14"><path d="M5 0h4v5h5v4H9v5H5V9H0V5h5z" fill="#f07a1f"/></svg>What typs of insurance do you accept?</div>
  </div>
</section>
<div class="divider abs"></div>
<section class="news abs">
  <h2 class="block-title heading">LATEST NEWS</h2>
  <article class="news-item">
    <div class="photo" role="img" aria-label="Photo of a girl in a denim jacket looking worried" style="background:linear-gradient(135deg,#b7c3cf,#6f88a6,#d8b99c)"></div>
    <div><h4>Lorem Ipsum is simply dummy text</h4><p class="date">▣ 10 JULY 2016</p><p>Lorem Ipsum is simply dummy text of the printing and typesetting industry......</p><span class="more">READ MORE &nbsp;»</span></div>
  </article>
  <article class="news-item">
    <div class="photo" role="img" aria-label="Photo of a parent helping a child with homework" style="background:linear-gradient(135deg,#d9c6a8,#8e7256,#c9d2da)"></div>
    <div><h4>Lorem Ipsum is simply dummy text</h4><p class="date">▣ 10 JULY 2016</p><p>Lorem Ipsum is simply dummy text of the printing and typesetting industry......</p><span class="more">READ MORE &nbsp;»</span></div>
  </article>
</section>

<section class="cta abs">
  <p>Lorem Ipsum is simply dummy text of the printing and typesetting industry. Lorem Ipsum has been the industry's standard dummy text ever since the 1500s, when an unknown printer took a galley of type and scrambled.</p>
  <span class="form-btn">NEW PATIENT FORM</span>
</section>

<footer class="footer abs" role="img" aria-label="Dimmed background photo of smiling people">
  <h5 class="abs" style="left:80px;top:55px">Quick Inquiry</h5>
  <div class="field" style="top:104px">Name*</div>
  <div class="field" style="top:150px">Email*</div>
  <div class="field" style="top:196px">Services*</div>
  <div class="field" style="top:242px;height:92px">Message*</div>
  <span class="btn submit">SUBMIT</span>

  <h5 class="abs" style="left:569px;top:55px">Our Services</h5>
  <ul class="links abs" style="left:569px;top:95px">
    <li>Home</li><li>About Us</li><li>Services</li><li>Conditions We Treat</li><li>New Patients</li><li>Contact Us</li>
  </ul>

  <h5 class="abs" style="left:873px;top:55px">Find Us</h5>
  <div class="find abs" style="left:873px;top:98px;width:310px;height:300px">
    <div class="row" style="top:0"><svg width="18" height="24" viewBox="0 0 18 24"><path d="M9 0a9 9 0 0 1 9 9c0 6-9 15-9 15S0 15 0 9a9 9 0 0 1 9-9z" fill="#f07a1f"/><circle cx="9" cy="9" r="3.5" fill="#3d3530"/></svg><span>Maplecrest Behavioral Healthcare<br>Lorem Ipsum is simply dummy<br>text printing and typesetting</span></div>
    <div class="row" style="top:88px"><svg width="20" height="20" viewBox="0 0 16 16"><path d="M3 1l3 1 1 4-2 1c1 2 2 3 4 4l1-2 4 1 1 3-2 2C7 15 1 9 1 3z" fill="#f07a1f"/></svg><span>+1-770-555-0148</span></div>
    <div class="row" style="top:132px"><svg width="20" height="20" viewBox="0 0 20 20"><rect x="1" y="6" width="18" height="13" rx="2" fill="#f07a1f"/><rect x="5" y="1" width="10" height="6" fill="none" stroke="#f07a1f" stroke-width="2"/></svg><span>+1-770-555-0149</span></div>
    <div class="row" style="top:176px"><svg width="22" height="16" viewBox="0 0 22 16"><rect width="22" height="16" rx="2" fill="#f07a1f"/><path d="M1 2l10 7 10-7" stroke="#3d3530" stroke-width="2" fill="none"/></svg><span>info@maplecresthealth.example</span></div>
    <span class="social" style="left:0;top:238px"></span>
    <span class="social" style="left:60px;top:238px"></span>
    <span class="social" style="left:120px;top:238px"></span>
  </div>
</footer>

<div class="copyright abs">© MAPLECREST BEHAVIORAL HEALTHCARE- 2017. All Rights Reserved</div>

</body>
</html>
```